FinTech company looking to revamp and expand client-facing interface for our financial models

Pellworth Engines currently has a very simple website that allows clients to interact with our financial models. We are looking to completely redesign the current site and add several extra pages to provide extra functionality. We want the design to have a modern, slick feel, that will work on both a desktop or a tablet. It should be straightforward for clients to move between different pages at any time, and clear from the layout how to interact with the more advanced features. We have included screenshots of existing pages in the attached design brief, as well as sketches of the functionality required by the new pages, but can't provide a direct link to the current site.
Target Market(s)
Professional investors that will be paying to access the interface
Industry/Entity Type
Finance
Number of Pages Required
4 page
Colors
Designer to choose colors to be used in the design.
Look and feel
Each slider illustrates characteristics of the customer's brand and the style your logo design should communicate.

```html
<!DOCTYPE html>
<html lang="en">
<head>
<meta charset="utf-8">
<title>Pellworth Engines – Models and Favourites</title>
<link href="https://fonts.googleapis.com/css2?family=Open+Sans:wght@400;600;700&display=swap" rel="stylesheet">
<style>
:root{
  --page:#d6d6d6;
  --sidebar:#31628f;
  --topbar:#1c2b36;
  --nav-active:#2a3b49;
  --main:#f2f2f2;
  --ink:#333;
  --muted:#4e5b66;
  --white:#fff;
  --green:#2e9b39;
  --teal:#27a07b;
  --link:#2e9b39;
  --row:#f6f5f5;
  --line:#dcdcdc;
}
*{box-sizing:border-box;margin:0;padding:0}
html,body{width:1100px;height:1200px;overflow:hidden}
body{background:var(--page);font-family:"Open Sans",Arial,sans-serif;color:var(--ink);position:relative}
.screen{position:absolute;left:88px;width:921px;height:498px;background:var(--main);overflow:hidden}
.screen--models{top:72px}
.screen--favourites{top:619px}
.sidebar{position:absolute;left:0;top:0;width:166px;height:457px;background:var(--sidebar);color:var(--white)}
.brand{position:absolute;left:28px;top:19px;font-weight:700;font-size:13px;letter-spacing:.3px}
.side-nav{list-style:none;position:absolute;top:77px;left:0;width:166px}
.side-nav li{height:29px;display:flex;align-items:center;padding-left:25px;font-size:8.5px;position:relative}
.side-nav svg{width:10px;height:10px;margin-right:5px;fill:var(--white)}
.side-nav .chev{position:absolute;right:10px;width:6px;height:6px;fill:none;stroke:var(--white);stroke-width:1.5;margin:0}
.topbar{position:absolute;left:166px;top:0;right:0;height:50px;background:var(--topbar);color:var(--white)}
.ranges{position:absolute;left:27px;top:0;height:50px;display:flex;align-items:center;gap:0;font-size:9.5px;color:#3b4c59}
.ranges span{margin-right:29px}
.tab{position:absolute;top:0;height:50px;width:90px;display:flex;align-items:center;justify-content:center;font-size:9.5px;letter-spacing:.2px}
.tab svg{width:9px;height:9px;fill:var(--white);margin-right:3px}
.tab--active{background:var(--nav-active)}
.content{position:absolute;left:166px;top:50px;right:0;height:407px}
.field{position:absolute;left:29px;display:flex;align-items:center;font-size:10px;height:19px}
.field .lead{width:50px}
.field sup{font-size:5px;margin-left:-23px;margin-right:12px;align-self:flex-start}
.field b{font-weight:600;margin-right:2px}
.field .input{width:165px;height:19px;background:var(--white);border:1px solid var(--line);font-size:7.5px;padding-left:6px;display:flex;align-items:center}
.field--quality{top:37px}
.field--abs{top:67px}
.export{position:absolute;left:29px;top:106px;font-size:8px;color:var(--link);display:flex;align-items:center}
.export svg{width:8px;height:8px;stroke:var(--link);fill:none;stroke-width:1.4;margin-right:1px}
.data{position:absolute;left:30px;top:136px;width:671px;border-collapse:collapse;table-layout:fixed;font-size:8.4px}
.data th{height:32px;color:var(--white);font-weight:400;font-size:9.8px;text-align:left;padding-left:7px;border-right:1px solid rgba(255,255,255,.25)}
.data--green th{background:var(--green)}
.data--teal th{background:var(--teal)}
.data td{height:34px;vertical-align:top;padding:7px 4px 0 7px;background:var(--row);border:1px solid var(--line);line-height:1.15}
.data td.num{text-align:center;padding-left:2px;padding-right:2px}
.data th .caret{display:inline-block;border-left:3px solid transparent;border-right:3px solid transparent;border-top:4px solid var(--white);margin-left:3px;vertical-align:middle}
.footer{position:absolute;left:0;right:0;bottom:0;height:41px;background:var(--topbar);color:#c9d1d8;font-size:7.5px}
.footer .legal{position:absolute;left:0;right:0;top:15px;text-align:center}
.footer .build{position:absolute;right:28px;top:15px}
</style>
</head>
<body>

<section class="screen screen--models">
  <aside class="sidebar">
    <div class="brand">PELLWORTH</div>
    <ul class="side-nav">
      <li><svg viewBox="0 0 10 10"><path d="M1 8a4 4 0 1 1 8 0z"/></svg>Dashboard</li>
      <li><svg viewBox="0 0 10 10"><path d="M5 1l4 4H8v4H6V6H4v3H2V5H1z"/></svg>Main<svg class="chev" viewBox="0 0 6 6"><path d="M1 2l2 2 2-2"/></svg></li>
      <li><svg viewBox="0 0 10 10"><rect x="1" y="2" width="8" height="7"/></svg>Calendar</li>
      <li><svg viewBox="0 0 10 10"><rect x="1" y="5" width="2" height="4"/><rect x="4" y="3" width="2" height="6"/><rect x="7" y="1" width="2" height="8"/></svg>Reports</li>
      <li><svg viewBox="0 0 10 10"><rect x="1" y="1" width="8" height="6"/><rect x="4" y="7" width="2" height="2"/></svg>Self Service</li>
      <li><svg viewBox="0 0 10 10"><rect x="2" y="1" width="6" height="8"/></svg>Documents</li>
      <li><svg viewBox="0 0 10 10"><rect x="1" y="3" width="8" height="5" transform="rotate(-15 5 5)"/></svg>Payroll</li>
      <li><svg viewBox="0 0 10 10"><circle cx="4" cy="6" r="3"/><circle cx="7.5" cy="2.5" r="2"/></svg>Settings<svg class="chev" viewBox="0 0 6 6"><path d="M1 2l2 2 2-2"/></svg></li>
      <li><svg viewBox="0 0 10 10"><path d="M3 3a2 2 0 1 1 3 2L5 6v1H4V5.5L5 4.5A1 1 0 1 0 4 3zM4 8h1v1H4z"/></svg>Help<svg class="chev" viewBox="0 0 6 6"><path d="M1 2l2 2 2-2"/></svg></li>
    </ul>
  </aside>
  <header class="topbar">
    <div class="ranges"><span>250D</span><span>83D</span><span>42D</span></div>
    <div class="tab tab--active" style="left:366px"><svg viewBox="0 0 10 10"><path d="M5 1l4 4H8v4H6V6H4v3H2V5H1z"/></svg>MODELS</div>
    <div class="tab" style="left:489px;width:110px"><svg viewBox="0 0 10 10"><circle cx="5" cy="5" r="3.5" fill="none" stroke="#fff" stroke-width="1.4"/></svg>SENSITIVITIES</div>
    <div class="tab" style="left:622px;width:110px"><svg viewBox="0 0 10 10"><path d="M5 .5l1.3 3h3.2L7 5.6l1 3.4L5 7.1 2 9l1-3.4L.5 3.5h3.2z"/></svg>FAVOURITES</div>
  </header>
  <main class="content">
    <div class="field field--quality"><span class="lead">Quality</span><b>Threshold:</b><span class="input">-10</span></div>
    <div class="field field--abs"><span class="lead">Abs.</span><sup>Stat</sup><b>Threshold:</b><span class="input">-10</span></div>
    <div class="export"><svg viewBox="0 0 8 8"><path d="M1 7l6-6M4 1h3v3M1 4v3h3"/></svg>EXPORT</div>
    <table class="data data--green">
      <colgroup><col style="width:53px"><col style="width:67px"><col style="width:66px"><col style="width:64px"><col style="width:55px"><col style="width:53px"><col style="width:53px"><col style="width:49px"><col style="width:48px"><col style="width:54px"><col style="width:49px"><col style="width:60px"></colgroup>
      <thead><tr><th style="padding-left:17px">ID<span class="caret"></span></th><th>Sector</th><th>Time</th><th>Quality</th><th style="padding-left:16px">Stat 1</th><th>Stat 2</th><th>Stat 3</th><th>Stat 4</th><th>Stat 5</th><th>Stat 6</th><th>Stat 7</th><th>Stat 8</th></tr></thead>
      <tbody>
        <tr><td style="padding-left:13px">Model 1</td><td>Materials</td><td>2019-07-03<br>12:15:00.000</td><td>30.2288</td><td class="num">2.01574</td><td class="num">23.305</td><td class="num">-0.149368</td><td class="num">22.3054</td><td class="num">4.63714</td><td class="num">0.945706</td><td class="num">2.81949</td><td class="num">2.60858</td></tr>
        <tr><td style="padding-left:13px">Model 2</td><td>Industrials</td><td>2019-07-03<br>12:15:00.000</td><td>32.8694</td><td class="num">2.01574</td><td class="num">23.305</td><td class="num">-0.149368</td><td class="num">22.3054</td><td class="num">4.63714</td><td class="num">0.945706</td><td class="num">2.81949</td><td class="num">2.60858</td></tr>
        <tr><td style="padding-left:13px">Model 3</td><td>Consumer Discretionary</td><td>2019-07-03<br>12:15:00.000</td><td>30.2288</td><td class="num">2.01574</td><td class="num">23.305</td><td class="num">-0.149368</td><td class="num">22.3054</td><td class="num">4.63714</td><td class="num">0.945706</td><td class="num">2.81949</td><td class="num">2.60858</td></tr>
        <tr><td style="padding-left:13px">Model 4</td><td>Information Technology</td><td>2019-07-03<br>12:15:00.000</td><td>32.8694</td><td class="num">2.01574</td><td class="num">23.305</td><td class="num">-0.149368</td><td class="num">22.3054</td><td class="num">4.63714</td><td class="num">0.945706</td><td class="num">2.81949</td><td class="num">2.60858</td></tr>
        <tr><td style="padding-left:13px">Model 5</td><td>Information Technology</td><td>2019-07-03<br>12:15:00.000</td><td>30.2288</td><td class="num">2.01574</td><td class="num">23.305</td><td class="num">-0.149368</td><td class="num">22.3054</td><td class="num">4.63714</td><td class="num">0.945706</td><td class="num">2.81949</td><td class="num">2.60858</td></tr>
      </tbody>
    </table>
  </main>
  <footer class="footer"><div class="legal">© 2019 Pellworth . All right reserved.&nbsp; Term of Use</div><div class="build">C16</div></footer>
</section>

<section class="screen screen--favourites">
  <aside class="sidebar">
    <div class="brand">PELLWORTH</div>
    <ul class="side-nav">
      <li><svg viewBox="0 0 10 10"><path d="M1 8a4 4 0 1 1 8 0z"/></svg>Dashboard</li>
      <li><svg viewBox="0 0 10 10"><path d="M5 1l4 4H8v4H6V6H4v3H2V5H1z"/></svg>Main<svg class="chev" viewBox="0 0 6 6"><path d="M1 2l2 2 2-2"/></svg></li>
      <li><svg viewBox="0 0 10 10"><rect x="1" y="2" width="8" height="7"/></svg>Calendar</li>
      <li><svg viewBox="0 0 10 10"><rect x="1" y="5" width="2" height="4"/><rect x="4" y="3" width="2" height="6"/><rect x="7" y="1" width="2" height="8"/></svg>Reports</li>
      <li><svg viewBox="0 0 10 10"><rect x="1" y="1" width="8" height="6"/><rect x="4" y="7" width="2" height="2"/></svg>Self Service</li>
      <li><svg viewBox="0 0 10 10"><rect x="2" y="1" width="6" height="8"/></svg>Documents</li>
      <li><svg viewBox="0 0 10 10"><rect x="1" y="3" width="8" height="5" transform="rotate(-15 5 5)"/></svg>Payroll</li>
      <li><svg viewBox="0 0 10 10"><circle cx="4" cy="6" r="3"/><circle cx="7.5" cy="2.5" r="2"/></svg>Settings<svg class="chev" viewBox="0 0 6 6"><path d="M1 2l2 2 2-2"/></svg></li>
      <li><svg viewBox="0 0 10 10"><path d="M3 3a2 2 0 1 1 3 2L5 6v1H4V5.5L5 4.5A1 1 0 1 0 4 3zM4 8h1v1H4z"/></svg>Help<svg class="chev" viewBox="0 0 6 6"><path d="M1 2l2 2 2-2"/></svg></li>
    </ul>
  </aside>
  <header class="topbar">
    <div class="ranges"><span>250D</span><span>83D</span><span>42D</span></div>
    <div class="tab" style="left:359px"><svg viewBox="0 0 10 10"><path d="M5 1l4 4H8v4H6V6H4v3H2V5H1z"/></svg>MODELS</div>
    <div class="tab" style="left:473px;width:110px"><svg viewBox="0 0 10 10"><circle cx="5" cy="5" r="3.5" fill="none" stroke="#fff" stroke-width="1.4"/></svg>SENSITIVITIES</div>
    <div class="tab tab--active" style="left:612px"><svg viewBox="0 0 10 10"><path d="M5 .5l1.3 3h3.2L7 5.6l1 3.4L5 7.1 2 9l1-3.4L.5 3.5h3.2z"/></svg>FAVOURITES</div>
  </header>
  <main class="content">
    <div class="field field--quality"><span class="lead">Quality</span><b>Threshold:</b><span class="input">-10</span></div>
    <div class="field field--abs"><span class="lead">Abs.</span><sup>Stat</sup><b>Threshold:</b><span class="input">-10</span></div>
    <div class="export"><svg viewBox="0 0 8 8"><path d="M1 7l6-6M4 1h3v3M1 4v3h3"/></svg>EXPORT</div>
    <table class="data data--teal">
      <colgroup><col style="width:67px"><col style="width:66px"><col style="width:66px"><col style="width:57px"><col style="width:61px"><col style="width:50px"><col style="width:56px"><col style="width:48px"><col style="width:49px"><col style="width:49px"><col style="width:54px"><col style="width:48px"></colgroup>
      <thead><tr><th style="padding-left:17px">ID<span class="caret"></span></th><th>Sector</th><th>Time</th><th>Quality</th><th style="padding-left:20px">Stat 1</th><th>Stat 2</th><th>Stat 3</th><th>Stat 4</th><th>Stat 5</th><th>Stat 6</th><th>Stat 7</th><th>Stat 8</th></tr></thead>
      <tbody>
        <tr><td style="padding-left:13px">Favourite 1</td><td>Materials</td><td>2019-07-03<br>12:15:00.000</td><td>30.2288</td><td class="num">2.01574</td><td class="num">23.305</td><td class="num">-0.149368</td><td class="num">22.3054</td><td class="num">4.63714</td><td class="num">0.945706</td><td class="num">2.81949</td><td class="num">2.60858</td></tr>
        <tr><td style="padding-left:13px">Favourite 2</td><td>Industrials</td><td>2019-07-03<br>12:15:00.000</td><td>32.8694</td><td class="num">2.01574</td><td class="num">23.305</td><td class="num">-0.149368</td><td class="num">22.3054</td><td class="num">4.63714</td><td class="num">0.945706</td><td class="num">2.81949</td><td class="num">2.60858</td></tr>
        <tr><td style="padding-left:13px">Favourite 3</td><td>Consumer Discretionary</td><td>2019-07-03<br>12:15:00.000</td><td>30.2288</td><td class="num">2.01574</td><td class="num">23.305</td><td class="num">-0.149368</td><td class="num">22.3054</td><td class="num">4.63714</td><td class="num">0.945706</td><td class="num">2.81949</td><td class="num">2.60858</td></tr>
        <tr><td style="padding-left:13px">Favourite 4</td><td>Information Technology</td><td>2019-07-03<br>12:15:00.000</td><td>32.8694</td><td class="num">2.01574</td><td class="num">23.305</td><td class="num">-0.149368</td><td class="num">22.3054</td><td class="num">4.63714</td><td class="num">0.945706</td><td class="num">2.81949</td><td class="num">2.60858</td></tr>
        <tr><td style="padding-left:13px">Favourite 5</td><td>Information Technology</td><td>2019-07-03<br>12:15:00.000</td><td>30.2288</td><td class="num">2.01574</td><td class="num">23.305</td><td class="num">-0.149368</td><td class="num">22.3054</td><td class="num">4.63714</td><td class="num">0.945706</td><td class="num">2.81949</td><td class="num">2.60858</td></tr>
      </tbody>
    </table>
  </main>
  <footer class="footer"><div class="legal">© 2019 Pellworth . All right reserved.&nbsp; Term of Use</div><div class="build">C16</div></footer>
</section>

</body>
</html>
```